75%-100% OFF - Insulation Banner Design

Need banners created for an online marketing push for my insulation business Tivoran Energy.

www.tivoranenergy.com

Specifically - I would like the banners to pop utilizing our colors in neon. To see samples of colors we use - visit our asset folder.

https://files.quelmarsh.net/share/7kXpw20LmzQaRt5vYbNe83HsUd4cJf?view=open

I will attach sample files to this project.

The banner must highlight 75%-100% off Insulation and Weatherization. If you can include our current perfect Google reviews somewhere in the advertisement that would be awesome but not a requirement.

The banner must meet Hearthwise logo guidelines. Please see attachment.

Target Market(s)

Home Owners

Industry/Entity Type

Insulation and Construction

Font styles to use
Sans Serif

Colors
59FF00
82FF00
B8FF75
E3FFCB
F4FFEA

Requirements
Must have
• Hearthwise Logo per project description. Must have 75-100% off somewhere that is very clear. And must have our company Tivoran Energy Logo.
Nice to have
• Tivoran Energy Logo

```html
<!DOCTYPE html>
<html lang="en">
<head>
<meta charset="utf-8">
<title>Tivoran Energy – Insulation &amp; Weatherization Banners</title>
<link rel="stylesheet" href="https://fonts.googleapis.com/css2?family=Oswald:wght@400;500;600&display=swap">
<style>
  :root {
    --canvas-bg: #4b5a60;
    --neon: #59ff00;
    --lime-soft: #b8ff75;
    --orange: #ff4a06;
    --forest: #0f7a33;
    --ink: #161616;
    --charcoal: #333333;
    --sand: #e8e2da;
    --white: #ffffff;
    --wood-light: #8a6446;
    --wood-mid: #5a3b26;
    --wood-dark: #2e1e13;
    --shirt-green: #1fb36a;
    --fiber: #c8ad86;
    --sky: #eef0ef;
    --shed: #d8d2c2;
    --truck-green: #2f9a55;
    --truck-white: #f4f5f5;
    --yard: #b9b8b2;
  }
  * { box-sizing: border-box; margin: 0; padding: 0; }
  html, body { width: 1200px; height: 776px; overflow: hidden; }
  body {
    background: var(--canvas-bg);
    font-family: "Oswald", "Arial Narrow", sans-serif;
    position: relative;
  }
  .banner {
    position: absolute;
    left: 35px;
    width: 1130px;
    height: 353px;
    overflow: hidden;
  }
  .banner--attic { top: 24px; }
  .banner--fleet { top: 403px; background: var(--sand); }
  .banner svg.shapes { position: absolute; inset: 0; }
  .photo { position: absolute; }
  .photo--attic {
    left: 380px; top: 0; right: 0; bottom: 0;
    background:
      radial-gradient(ellipse 170px 120px at 62% 42%, rgba(31,179,106,0.85), rgba(31,179,106,0) 100%),
      radial-gradient(ellipse 200px 70px at 48% 82%, rgba(200,173,134,0.75), rgba(200,173,134,0) 100%),
      radial-gradient(ellipse 90px 60px at 90% 62%, rgba(230,230,225,0.55), rgba(230,230,225,0) 100%),
      radial-gradient(ellipse 260px 120px at 80% 12%, rgba(138,100,70,0.7), rgba(138,100,70,0) 100%),
      linear-gradient(170deg, var(--wood-mid) 0%, var(--wood-dark) 45%, var(--wood-mid) 75%, var(--wood-light) 100%);
  }
  .photo--fleet {
    left: 520px; top: 0; right: 0; bottom: 0;
    background:
      radial-gradient(ellipse 130px 60px at 52% 60%, rgba(47,154,85,0.8), rgba(47,154,85,0) 100%),
      radial-gradient(ellipse 110px 55px at 84% 60%, rgba(47,154,85,0.75), rgba(47,154,85,0) 100%),
      radial-gradient(ellipse 120px 55px at 40% 74%, rgba(244,245,245,0.95), rgba(244,245,245,0) 100%),
      radial-gradient(ellipse 110px 55px at 68% 76%, rgba(244,245,245,0.95), rgba(244,245,245,0) 100%),
      radial-gradient(ellipse 90px 55px at 95% 80%, rgba(250,250,250,0.95), rgba(250,250,250,0) 100%),
      radial-gradient(ellipse 220px 90px at 85% 30%, rgba(216,210,194,0.9), rgba(216,210,194,0) 100%),
      linear-gradient(180deg, var(--sky) 0%, #e6e8e7 45%, var(--yard) 82%, #cfcdc6 100%);
  }
  .photo--fleet::before {
    content: "";
    position: absolute; inset: 0;
    background: linear-gradient(90deg, var(--sand) 0%, rgba(232,226,218,0) 30%);
  }
  .headline {
    position: absolute;
    text-transform: uppercase;
    font-weight: 600;
    line-height: 1;
    letter-spacing: 0.3px;
  }
  .headline span {
    display: block;
    width: max-content;
    text-shadow:
      0 0 0 var(--white),
      4px 0 0 var(--white), -4px 0 0 var(--white),
      0 4px 0 var(--white), 0 -4px 0 var(--white),
      3px 3px 0 var(--white), -3px 3px 0 var(--white),
      3px -3px 0 var(--white), -3px -3px 0 var(--white),
      6px 0 0 var(--white), -6px 0 0 var(--white),
      0 6px 0 var(--white), 0 -6px 0 var(--white),
      5px 4px 0 var(--white), -5px 4px 0 var(--white),
      5px -4px 0 var(--white), -5px -4px 0 var(--white),
      2px 4px 6px rgba(0,0,0,0.25);
  }
  .headline .accent-orange { color: var(--orange); }
  .headline .accent-forest { color: var(--forest); }
  .banner--attic .headline { left: 28px; top: 32px; font-size: 56px; }
  .banner--attic .headline span { margin-bottom: 0; }
  .banner--fleet .headline {
    left: 346px; top: 72px; font-size: 48px;
    transform: scaleX(0.86); transform-origin: left top;
  }
  .banner--fleet .headline span { margin-bottom: -1px; }
  .offer-attic { position: absolute; left: 21px; top: 232px; color: var(--ink); }
  .offer-attic .upto { font-size: 36px; font-weight: 500; line-height: 1; color: var(--charcoal); }
  .offer-attic .amount { font-size: 54px; font-weight: 500; line-height: 1.12; }
  .badge {
    position: absolute;
    left: 447px; top: 94px;
    width: 166px; height: 166px;
    border-radius: 50%;
    background: var(--neon);
    border: 5px solid var(--white);
    display: flex; align-items: center; justify-content: center;
    text-align: center;
  }
  .brand-name {
    font-weight: 600;
    color: var(--ink);
    text-transform: uppercase;
    line-height: 1;
  }
  .badge .brand-name { font-size: 26px; }
  .fleet-brand {
    position: absolute; left: 26px; top: 40px;
    display: flex; align-items: center; gap: 12px;
  }
  .fleet-brand .mark { width: 22px; height: 22px; background: var(--ink); }
  .fleet-brand .brand-name { font-size: 40px; line-height: 1.02; }
  .offer-fleet {
    position: absolute; left: 20px; top: 224px;
    display: flex; align-items: center; gap: 14px;
  }
  .offer-fleet .upto { color: var(--neon); font-size: 36px; font-weight: 500; padding-top: 20px; }
  .offer-fleet .amount { color: var(--white); font-size: 52px; font-weight: 500; line-height: 1; }
  .cta {
    position: absolute; left: 347px; top: 236px;
    width: 127px; height: 40px;
    border: 1.5px solid var(--charcoal);
    color: var(--charcoal);
    font-size: 15px; font-weight: 500;
    display: flex; align-items: center; justify-content: center;
    text-transform: uppercase; letter-spacing: 0.5px;
    background: transparent;
  }
</style>
</head>
<body>

  <section class="banner banner--attic">
    <div class="photo photo--attic" role="img" aria-label="Installer in green work shirt, mask and gloves fitting insulation between attic rafters"></div>
    <svg class="shapes" width="1130" height="353" viewBox="0 0 1130 353">
      <polygon points="402,0 418,0 510,174 415,353 399,353 494,174" fill="#2c2c2c"/>
      <polygon points="0,0 402,0 494,174 399,353 0,353" fill="var(--lime-soft)"/>
    </svg>
    <h2 class="headline">
      <span class="accent-orange">Insulation &amp;</span>
      <span class="accent-forest">Weatherization</span>
      <span class="accent-orange">Energy Savings</span>
    </h2>
    <div class="offer-attic">
      <div class="upto">UPTO</div>
      <div class="amount">75%-100% OFF</div>
    </div>
    <div class="badge"><div class="brand-name">Tivoran<br>Energy</div></div>
  </section>

  <section class="banner banner--fleet">
    <div class="photo photo--fleet" role="img" aria-label="Branded white and green service trucks and vans parked outside a warehouse"></div>
    <svg class="shapes" width="1130" height="353" viewBox="0 0 1130 353">
      <polygon points="368,0 390,22 220,190 196,176" fill="var(--lime-soft)"/>
      <polygon points="0,0 368,0 196,176 0,176" fill="var(--neon)"/>
      <polygon points="0,176 196,176 395,353 0,353" fill="var(--charcoal)"/>
      <polygon points="1130,262 1130,353 1040,353" fill="var(--lime-soft)"/>
      <polygon points="1130,275 1130,353 1056,353" fill="var(--neon)"/>
    </svg>
    <div class="fleet-brand">
      <div class="mark"></div>
      <div class="brand-name">Tivoran<br>Energy</div>
    </div>
    <div class="offer-fleet">
      <div class="upto">UPTO</div>
      <div class="amount">75%-<br>100% OFF</div>
    </div>
    <h2 class="headline">
      <span class="accent-orange">Insulation &amp;</span>
      <span class="accent-forest">Weatherization</span>
      <span class="accent-orange">Energy Savings</span>
    </h2>
    <a class="cta">Learn More</a>
  </section>

</body>
</html>
```